Hi Designers,

I will need 4 web pages designed. The web page looks like an App (if you click on the logo, or the icon on an iPad, it will take you to the website), but it is still a webpage.

Please check the attachment on this brief to understand what specific pages I need to be designed.

A .PSD (straight-up PhotoShop image) as final deliverable is fine, as long as you give us the exact “web color numbers”.

The design is for desktop and iPad but in a single unified web application, NOT separate web app and (native) iPad app.

Details:

Brightwater Policy Partners is developing a browser-based application for use on any mobile device or desktop. The app will be used by corporations to communicate with their employees regarding legal, regulatory and company requirements for conducting business. The app is known as “Harbor Guidance Portal.” When the user clicks on the icon for Harbor Guidance Portal, they will enter a site full of information that a company deems necessary for the employee to do his/her job. There are several content sections within the site, including a login page, training, policies, forms, news feeds and blogs.

The application has been built using Microsoft .NET, and fully supports CSS-type skinning; it uses traditional page layouts. We are seeking a product logo concept (image), a master application/desktop icon (image), as well as a full color scheme/theme/skin design for all areas of the application (header area, body text, menu bar, etc.) in the form of a CSS. The look should be clean, crisp and professional; nothing cartoony or whimsical. It should be easy to read and “airy”.

We have sketched prototypes for the basic application page layout that we can send as a next step of the process.
Updates

Screen shots have been uploaded to this project.  Please use them to guide your design.

Dear designers,

I apologize for the delay in providing feedback. My partners and I will provide feedback in a few days. Thank you for your patience.

Industry/Entity Type

Business

Font styles to use
Other font styles liked:
• see font on screen shots when uploaded

```html
<!DOCTYPE html>
<html lang="en">
<head>
<meta charset="utf-8">
<title>Harbor Guidance Portal – Login</title>
<link rel="stylesheet" href="https://fonts.googleapis.com/css2?family=Source+Sans+3:wght@300;400;600&family=PT+Sans+Narrow:wght@700&display=swap">
<style>
  :root {
    --teal: #00a9a8;
    --teal-title: #14a9a7;
    --teal-btn-top: #17c6c2;
    --teal-btn-bottom: #00a7a4;
    --navy: #05294e;
    --navy-dark: #021a33;
    --bg-center: #fbfbfb;
    --bg-edge: #e4e4e4;
    --panel: #f6f6f6;
    --panel-border: #ffffff;
    --field: #ffffff;
    --field-border: #e2e2e2;
    --placeholder: #a9a9a9;
    --text: #3f3f3f;
    --white: #ffffff;
  }
  * { box-sizing: border-box; margin: 0; padding: 0; }
  html, body { width: 1200px; height: 740px; overflow: hidden; }
  body {
    position: relative;
    font-family: "Source Sans 3", Arial, sans-serif;
    background: radial-gradient(ellipse 620px 520px at 600px 330px, var(--bg-center) 0%, #f1f1f1 55%, var(--bg-edge) 100%);
  }

  .brand-tab {
    position: absolute; left: 421px; top: 46px; width: 355px; height: 104px;
    background: linear-gradient(180deg, var(--navy) 0%, var(--navy) 75%, var(--navy-dark) 100%);
    border: 1px solid #c9ccd1; border-bottom: none; border-radius: 4px 4px 0 0;
    box-shadow: 0 6px 22px rgba(0,0,0,.35);
    display: flex; align-items: center; justify-content: center; gap: 16px;
    padding-bottom: 8px;
  }
  .brand-tab .brand-dot { width: 40px; height: 40px; border-radius: 50%; background: #4a88c7; }
  .brand-tab .brand-name { color: var(--white); font-size: 21px; font-weight: 400; }

  .login-panel {
    position: absolute; left: 290px; top: 147px; width: 620px; height: 338px;
    background: var(--panel);
    border: 2px solid var(--panel-border); border-radius: 7px;
    box-shadow: 0 14px 18px -10px rgba(0,0,0,.28), 0 0 3px rgba(0,0,0,.08);
  }
  .login-title {
    position: absolute; left: 78px; top: 18px;
    font-family: "PT Sans Narrow", "Arial Narrow", sans-serif;
    font-weight: 700; font-size: 24px; color: var(--teal-title); letter-spacing: .2px;
  }
  .field {
    position: absolute; left: 78px; width: 459px; height: 55px;
    background: var(--field); border: 1px solid var(--field-border); border-radius: 3px;
    box-shadow: inset 0 1px 2px rgba(0,0,0,.06);
    padding-left: 13px; line-height: 53px;
    font-size: 15px; font-weight: 300; color: var(--placeholder);
  }
  .field-username { top: 67px; }
  .field-password { top: 147px; }
  .options {
    position: absolute; left: 79px; top: 220px;
    display: flex; align-items: center; font-size: 12.5px; color: var(--text);
  }
  .checkbox {
    width: 13px; height: 13px; border: 1px solid #8a8a8a; background: linear-gradient(#fff,#e6e6e6);
    margin-right: 17px;
  }
  .options .sep { margin: 0 7px; }
  .sign-in {
    position: absolute; left: 78px; top: 255px; width: 117px; height: 40px;
    background: linear-gradient(180deg, var(--teal-btn-top), var(--teal-btn-bottom));
    border: 1px solid #079c98; border-radius: 2px;
    box-shadow: 0 1px 2px rgba(0,0,0,.25);
    color: var(--white); font-family: "PT Sans Narrow", "Arial Narrow", sans-serif;
    font-weight: 700; font-size: 18px; text-align: center; line-height: 38px;
  }

  .portal-mark {
    position: absolute; left: 408px; top: 533px;
    display: flex; align-items: center; gap: 11px;
  }
  .portal-mark .mark-square { width: 55px; height: 55px; background: var(--teal); }
  .portal-mark .mark-name {
    font-size: 19px; font-weight: 400; color: var(--teal);
    text-transform: uppercase; letter-spacing: 1px;
  }

  .site-footer {
    position: absolute; left: 0; top: 632px; width: 1200px; height: 108px;
    background: var(--teal);
  }
  .copyright {
    position: absolute; left: 420px; top: 44px;
    color: var(--white); font-size: 14px; font-weight: 300; letter-spacing: -.2px;
    white-space: pre;
  }
</style>
</head>
<body>
  <header class="brand-tab">
    <span class="brand-dot"></span>
    <span class="brand-name">Corvane Health</span>
  </header>

  <main class="login-panel">
    <h1 class="login-title">LOGIN PANEL</h1>
    <div class="field field-username">Username</div>
    <div class="field field-password">Password</div>
    <div class="options">
      <span class="checkbox"></span>
      <span>Keep me signed in</span><span class="sep">|</span><span>Forgot Password</span>
    </div>
    <div class="sign-in">Sign In</div>
  </main>

  <div class="portal-mark">
    <span class="mark-square"></span>
    <span class="mark-name">Harbor Guidance Portal</span>
  </div>

  <footer class="site-footer">
    <p class="copyright">Copyright ©2013 Company Name    - All rights reserved</p>
  </footer>
</body>
</html>
```